I need a flyer made , the flyer can be one page or two pages or three pages . I will be posting this on Instagram and social media platforms. I am a luxury home builder , I am looking to hire a construction project manager . Below are some examples and ideas what can be on the flyer

We’re looking for a construction project manager who’s passionate about building luxury homes at the highest standards
We’re hiring construction project manager
* Experience 5+ years in residential project management with a strong portfolio of completed homes.
* location : Bergen County NJ
* excellent leadership skills, leads teams with confidence and clarity
* communicates seamlessly with architects , engineers, designers and clients
*knows how to manage budgets and timelines without compromising quality
*solves problems with a positive solution first mindset
* pays attention to every detail because in luxury the small things are the big things

Apply now , link in bio or DM to connect.

My logo is attached, my web site www.velstridebuilders.com
My style is modern but still warm and inviting. I like a clean classy look .

Please don’t add any images of chairs or people to the flyer , I do not want people on my flyer. Do not add standard images of offices and houses , we are luxury builders , we build homes over 2 million dollars. Keep a classy , simple modern look . High end .

You can add a white hard hat with my logo on it for a image , this is a suggestion does not have to be on my flyer ,

```html
<!DOCTYPE html>
<html lang="en">
<head>
<meta charset="utf-8">
<title>Velstride Builders – Hiring Construction Project Manager</title>
<link rel="stylesheet" href="https://fonts.googleapis.com/css2?family=Montserrat:ital,wght@0,400;0,500;0,600;0,700;0,800;1,400;1,700&display=swap">
<style>
  :root {
    --ink: #0f0e0f;
    --paper: #ffffff;
    --mist-light: #fbfbfb;
    --mist-dark: #e4e4e4;
    --rule: #2a2a2a;
    --panel-rule: #4a4a4a;
    --panel-text: #ffffff;
  }
  * { margin: 0; padding: 0; box-sizing: border-box; }
  html, body { width: 1200px; height: 1200px; overflow: hidden; background: var(--paper); }
  body { font-family: "Montserrat", Arial, sans-serif; color: var(--ink); }
  .flyer { position: relative; width: 1200px; height: 1200px; overflow: hidden; background: var(--paper); }
  .backdrop { position: absolute; left: 0; top: 0; width: 1200px; height: 820px;
    background: radial-gradient(ellipse at 75% 35%, var(--mist-dark) 0%, #efefef 35%, var(--mist-light) 70%, var(--paper) 100%); }
  .abs { position: absolute; }
  .kicker { left: 446px; top: 100px; font-size: 54px; font-weight: 800; letter-spacing: 9px; line-height: 1; }
  .headline { left: 76px; top: 112px; font-size: 196px; font-weight: 700; letter-spacing: -5px; line-height: 1; }
  .role-eyebrow { left: 83px; top: 332px; font-size: 36px; font-weight: 500; letter-spacing: 6px; line-height: 1; }
  .role-title { left: 80px; top: 360px; font-size: 99px; font-weight: 700; line-height: 0.89; letter-spacing: -1px; }
  .brand { left: 805px; top: 112px; width: 345px; text-align: center; font-weight: 400; color: var(--ink); }
  .brand-name { font-size: 56px; letter-spacing: 2px; line-height: 1; }
  .brand-sub { font-size: 18px; letter-spacing: 4px; margin-top: 14px; line-height: 1; }
  .experience { left: 815px; top: 420px; }
  .experience-number { font-size: 100px; font-weight: 700; line-height: 1; letter-spacing: -2px; display: inline-block; }
  .experience-unit { font-size: 44px; font-weight: 700; display: inline-block; margin-left: 24px; vertical-align: 6px; }
  .experience-label { font-size: 50px; font-weight: 400; line-height: 1; margin-top: -6px; letter-spacing: 0.5px; }
  .rule { height: 1.5px; background: var(--rule); }
  .rule-main { left: 83px; top: 562px; width: 1046px; }
  .rule-side { left: 817px; top: 710px; width: 312px; }
  .field { left: 821px; top: 582px; font-size: 34px; font-weight: 700; line-height: 1.04; letter-spacing: 0.5px; }
  .portfolio { left: 821px; top: 728px; font-size: 25px; font-weight: 400; line-height: 1.2; letter-spacing: 0.8px; }
  .qualities-panel { left: 0; top: 595px; width: 740px; height: 425px; }
  .qualities { position: absolute; left: 0; top: 0; width: 740px; list-style: none; color: var(--panel-text); }
  .quality { position: absolute; left: 95px; display: flex; align-items: flex-start; gap: 10px; }
  .quality-tick { width: 21px; height: 21px; margin-top: 8px; flex: none; }
  .quality-title { font-size: 20px; font-weight: 700; line-height: 1.15; }
  .quality-detail { font-size: 17px; font-weight: 500; line-height: 1.2; }
  .location { left: 696px; top: 819px; width: 504px; height: 110px; }
  .location-text { position: absolute; right: 71px; top: 12px; text-align: right; color: var(--panel-text); }
  .location-label { font-size: 24px; font-weight: 700; letter-spacing: 5px; line-height: 1.3; }
  .location-value { font-size: 38px; font-weight: 700; line-height: 1.2; }
  .cta { left: 748px; top: 965px; font-size: 76px; font-weight: 700; line-height: 1; letter-spacing: -0.5px; }
  .cta-note { left: 751px; top: 1048px; font-size: 25px; font-weight: 500; }
  .social { left: 751px; top: 1102px; display: flex; align-items: center; gap: 16px; }
  .social-dot { width: 36px; height: 36px; border-radius: 50%; background: var(--ink); }
  .social-handle { font-size: 28px; font-weight: 700; }
  .tagline { left: 83px; top: 1054px; font-size: 26px; font-style: italic; font-weight: 400; letter-spacing: 2.5px; }
  .tagline strong { font-weight: 700; }
  .website { left: 85px; top: 1110px; font-size: 34px; font-weight: 700; letter-spacing: 0.3px; }
</style>
</head>
<body>
<main class="flyer">
  <div class="backdrop" role="img" aria-label="Faded architectural floor plan with drafting tools in soft greys"></div>

  <div class="abs kicker">WE’RE</div>
  <h1 class="abs headline">Hiring</h1>

  <div class="abs brand">
    <div class="brand-name">VELSTRIDE</div>
    <div class="brand-sub">builders</div>
  </div>

  <div class="abs role-eyebrow">CONSTRUCTION</div>
  <h2 class="abs role-title">PROJECT<br>MANAGER</h2>

  <div class="abs experience">
    <span class="experience-number">5+</span><span class="experience-unit">YEARS</span>
    <div class="experience-label">EXPERIENCE</div>
  </div>

  <div class="abs rule rule-main"></div>

  <div class="abs field">IN RESIDENTIAL<br>PROJECT<br>MANAGEMENT</div>
  <div class="abs rule rule-side"></div>
  <p class="abs portfolio">with a strong portfolio<br>of completed homes</p>

  <div class="abs qualities-panel">
    <svg width="740" height="425" viewBox="0 0 740 425" aria-hidden="true">
      <path d="M0 0 H714 Q740 0 736 26 L664 398 Q658 425 630 425 H0 Z" fill="var(--ink)"/>
      <g stroke="var(--panel-rule)" stroke-width="1.2">
        <line x1="122" y1="102" x2="700" y2="102"/>
        <line x1="122" y1="179" x2="682" y2="179"/>
        <line x1="122" y1="250" x2="668" y2="250"/>
        <line x1="122" y1="326" x2="653" y2="326"/>
      </g>
    </svg>
    <ul class="qualities">
      <li class="quality" style="top:40px">
        <svg class="quality-tick" viewBox="0 0 22 22"><circle cx="11" cy="11" r="9.5" fill="none" stroke="#fff" stroke-width="1.8"/><path d="M6.8 11.2l3 3 5.6-6" fill="none" stroke="#fff" stroke-width="1.8"/></svg>
        <div><div class="quality-title">Excellent leadership skills</div><div class="quality-detail">leads teams with confidence and clarity</div></div>
      </li>
      <li class="quality" style="top:113px">
        <svg class="quality-tick" viewBox="0 0 22 22"><circle cx="11" cy="11" r="9.5" fill="none" stroke="#fff" stroke-width="1.8"/><path d="M6.8 11.2l3 3 5.6-6" fill="none" stroke="#fff" stroke-width="1.8"/></svg>
        <div><div class="quality-title">Communicates seamlessly</div><div class="quality-detail">with architects, engineers, designers and clients</div></div>
      </li>
      <li class="quality" style="top:187px">
        <svg class="quality-tick" viewBox="0 0 22 22"><circle cx="11" cy="11" r="9.5" fill="none" stroke="#fff" stroke-width="1.8"/><path d="M6.8 11.2l3 3 5.6-6" fill="none" stroke="#fff" stroke-width="1.8"/></svg>
        <div><div class="quality-title">Knows how to manage</div><div class="quality-detail">budgets and timelines without compromising quality</div></div>
      </li>
      <li class="quality" style="top:261px">
        <svg class="quality-tick" viewBox="0 0 22 22"><circle cx="11" cy="11" r="9.5" fill="none" stroke="#fff" stroke-width="1.8"/><path d="M6.8 11.2l3 3 5.6-6" fill="none" stroke="#fff" stroke-width="1.8"/></svg>
        <div><div class="quality-title">Solves problems</div><div class="quality-detail">with a positive solution first mindset</div></div>
      </li>
      <li class="quality" style="top:335px">
        <svg class="quality-tick" viewBox="0 0 22 22"><circle cx="11" cy="11" r="9.5" fill="none" stroke="#fff" stroke-width="1.8"/><path d="M6.8 11.2l3 3 5.6-6" fill="none" stroke="#fff" stroke-width="1.8"/></svg>
        <div><div class="quality-title">Pays attention to every detail</div><div class="quality-detail">because in luxury the small things are the big things</div></div>
      </li>
    </ul>
  </div>

  <div class="abs location">
    <svg width="504" height="110" viewBox="0 0 504 110" aria-hidden="true">
      <path d="M30 0 H504 V110 H12 Q0 110 2 98 L18 12 Q20 0 30 0 Z" fill="var(--ink)"/>
    </svg>
    <div class="location-text">
      <div class="location-label">LOCATION</div>
      <div class="location-value">Bergen County, NJ</div>
    </div>
  </div>

  <div class="abs cta">Apply Now</div>
  <div class="abs cta-note">Link in Bio or DM to connect.</div>
  <div class="abs social"><span class="social-dot"></span><span class="social-handle">velstridebuilders</span></div>

  <p class="abs tagline">Build <strong>Luxury</strong>. Lead <strong>Excellence.</strong></p>
  <div class="abs website">www.velstridebuilders.com</div>
</main>
</body>
</html>
```